International business needs business cards

Our company, DRV Ventures Inc. is in the business of supplying a range construction products with particular emphasis on CEMENT. We have developed our own brand - TORVAN SUPPLIES - with which to infiltrate the market. We are launching our brand of cement (TORVAN Type IS Cement) into the Caribbean which is unlike anything this market has ever seen. A monopoly has existed here for the past 60-odd years and the market has now opened to allow the importation of other brands and consumers are anxious and ready for change/improvement. We are very excited to be launching and want to make a great first impression. We will be conducting workshops and seminars (from government level to the hardware store owners) and we want our business card to give us the strong, confident introduction that we need.

Target Market(s)

construction; builders; engineers; home owners

Industry/Entity Type

Construction

Contact Information for Business Card

Marisol Depree
CEO
cell # 1 555 4180736
Ground floor,Lindell Plaza Suite 2734
George Town,Grand Cayman
Cayman Islands,KY1-4823
EMAIL: m.depree@drvventuresinc.example
web site drvventuresinc.example

COMPANY: skype info drv.ventures.example

second card
Yvette Brannock-Depree
CFO
CELL# 1 555 607 3941
George Town,Grand Cayman
Cayman Islands,KY1-4823
EMAIL: y.brannockdepree@drvventuresinc.example
website drvventuresinc.example

Requirements
Must have
• Business cards must display BOTH logos - DRV is the company and TORVAN is the brand.

```html
<!DOCTYPE html>
<html lang="en">
<head>
<meta charset="utf-8">
<title>DRV Ventures Inc. — Business Card</title>
<link href="https://fonts.googleapis.com/css2?family=Source+Sans+3:wght@400;600;700&display=swap" rel="stylesheet">
<style>
  :root {
    --canvas: #e9e7e4;
    --card: #121212;
    --card-edge: #1c1c1c;
    --ink: #f2f2f2;
    --accent: #9c1b1f;
    --accent-name: #b3262b;
    --muted: #bfbfbf;
    --divider: #5a5a5a;
  }
  * { margin: 0; padding: 0; box-sizing: border-box; }
  html, body {
    width: 1200px; height: 814px; overflow: hidden;
    background: var(--canvas);
    font-family: "Source Sans 3", "Segoe UI", sans-serif;
  }
  .sheet {
    position: relative; width: 1200px; height: 814px;
    display: flex; align-items: center; justify-content: center; gap: 40px;
  }
  .card {
    position: relative; width: 540px; height: 309px;
    background: var(--card);
    border: 1px solid var(--card-edge);
    box-shadow: 0 10px 28px rgba(0,0,0,.25);
    color: var(--ink);
  }
  /* front */
  .brand {
    position: absolute; left: 40px; top: 196px;
    display: flex; align-items: center; gap: 12px;
  }
  .brand-square { width: 54px; height: 54px; background: var(--accent); }
  .brand-name {
    font-weight: 700; font-size: 27px; line-height: 1; color: var(--ink);
    letter-spacing: .5px;
  }
  .divider {
    position: absolute; left: 278px; top: 30px; width: 1px; height: 250px;
    background: linear-gradient(to bottom, transparent, var(--divider) 20%, var(--divider) 80%, transparent);
  }
  .contact {
    position: absolute; left: 296px; top: 36px; font-size: 14.5px; line-height: 18px;
  }
  .contact-name { color: var(--accent-name); font-size: 16px; font-weight: 600; }
  .contact-address { margin-bottom: 8px; }
  .contact-line { display: flex; align-items: center; gap: 8px; }
  .contact-line svg { width: 12px; height: 12px; flex: none; }
  /* back */
  .card-back { display: flex; flex-direction: column; align-items: center; }
  .brand-back {
    margin-top: 70px; display: flex; flex-direction: column; align-items: center; gap: 14px;
  }
  .brand-back-circle { width: 70px; height: 70px; border-radius: 50%; background: #3a3a3a; }
  .brand-back-name { font-weight: 700; font-size: 24px; color: #9a9a9a; letter-spacing: 3px; }
  .web {
    margin-top: 40px; font-size: 13px; letter-spacing: 1.6px; color: var(--muted);
  }
</style>
</head>
<body>
<main class="sheet">
  <section class="card card-front">
    <div class="brand">
      <span class="brand-square"></span>
      <span class="brand-name">DRV Ventures Inc.</span>
    </div>
    <div class="divider"></div>
    <div class="contact">
      <p class="contact-name">Marisol Depree</p>
      <p>CEO</p>
      <p class="contact-address">Ground floor<br>Lindell Plaza Suite 2734<br>George Town,Grand Cayman<br>Cayman Islands,KY1-4823</p>
      <p class="contact-line">
        <svg viewBox="0 0 12 12"><rect x="3" y="0.5" width="6" height="11" rx="1" fill="none" stroke="#b3262b" stroke-width="1.4"/><circle cx="6" cy="9.5" r=".8" fill="#b3262b"/></svg>
        1 555 4180736
      </p>
      <p class="contact-line">
        <svg viewBox="0 0 12 12"><rect x="0.5" y="2.5" width="11" height="7.5" fill="#b3262b"/><path d="M0.5 2.5 6 7l5.5-4.5" fill="none" stroke="#121212" stroke-width="1"/></svg>
        m.depree@drvventuresinc.example
      </p>
      <p class="contact-line">
        <svg viewBox="0 0 12 12"><circle cx="6" cy="6" r="5.5" fill="#b3262b"/><path d="M.5 6h11M6 .5c-3 3-3 8 0 11M6 .5c3 3 3 8 0 11" fill="none" stroke="#121212" stroke-width=".8"/></svg>
        drvventuresinc.example
      </p>
    </div>
  </section>

  <section class="card card-back">
    <div class="brand-back">
      <span class="brand-back-circle"></span>
      <span class="brand-back-name">TORVAN SUPPLIES</span>
    </div>
    <p class="web">www.drvventuresinc.example</p>
  </section>
</main>
</body>
</html>
```